Fun, Clean Business Card For Family Focused Travel Agency

I need a business card using specific colors and fonts as in the uploaded files. Ideally, I would like a large image of the logo on the back and all the contact info on the front. Maybe the stars/dots somewhere in a flowy form.

I do want it the contact information to be clear and easy to read. I don't want it to look too busy. Maybe even a bit minimalist.

I plan or ordering the ROUNDED CORNER business cards from Cardwell Press, so please consider that in your design.

Target Market(s)

Families with children, couples, groups of friends

Contact Information for Business Card

Marla Quint, Owner
Marla@TumbleTrips.example
Cell Phone Number 555-218-4603
Office Phone Number 555-647-1925
Specializing in Glimmerland destinations, Pelican Bay Fun Park, Cruises and All-Inclusive Vacations.

Nice but not required:
www.TumbleTrips.example
Facebook, Instagram, Twitter icons with username: TumbleTrips

Font styles to use
Sans Serif

Requirements
Must have
• Please try to use the colors from the logo as much as possible. I understand lighter shades/colors may be needed for some things.
Should not have
• NO SERIF FONTS. That is really the only thing I do not want at all

```html
<!DOCTYPE html>
<html lang="en">
<head>
<meta charset="utf-8">
<title>Tumble Trips – Business Card</title>
<link rel="stylesheet" href="https://fonts.googleapis.com/css2?family=Oswald:wght@500&family=Work+Sans:wght@400;500;600&display=swap">
<style>
  :root {
    --backdrop: #1c1c1c;
    --card: #262626;
    --card-edge: #2e2e2e;
    --accent: #f47c20;
    --ink: #f4f4f4;
    --ink-soft: #d8d8d8;
  }
  * { box-sizing: border-box; margin: 0; padding: 0; }
  html, body { width: 1200px; height: 900px; overflow: hidden; }
  body {
    background: var(--backdrop);
    font-family: "Work Sans", sans-serif;
    color: var(--ink);
    position: relative;
  }
  .card {
    position: absolute;
    left: 290px;
    width: 620px;
    height: 354px;
    background: linear-gradient(135deg, var(--card) 0%, var(--card-edge) 70%, #343434 100%);
    border-bottom: 5px solid var(--accent);
    box-shadow: 0 18px 40px rgba(0,0,0,.55);
  }
  .card--front { top: 68px; }
  .card--back { top: 470px; }

  /* Front */
  .brand {
    position: absolute;
    top: 96px; left: 0; right: 0;
    display: flex; align-items: center; justify-content: center; gap: 16px;
  }
  .brand__dot {
    width: 54px; height: 54px; border-radius: 50%;
    background: var(--ink);
  }
  .brand__name {
    font-family: "Work Sans", sans-serif;
    font-weight: 600;
    font-size: 58px;
    letter-spacing: -0.5px;
    color: var(--ink);
  }
  .tagline {
    position: absolute;
    top: 228px; left: 60px; right: 60px;
    text-align: center;
    font-size: 15px;
    line-height: 1.45;
    letter-spacing: .3px;
    color: var(--ink-soft);
  }

  /* Back */
  .person {
    position: absolute;
    top: 118px; right: 352px;
    text-align: right;
  }
  .person__name {
    font-family: "Oswald", sans-serif;
    font-weight: 500;
    font-size: 40px;
    letter-spacing: 2px;
    color: var(--accent);
    line-height: 1;
    text-transform: uppercase;
  }
  .person__role {
    margin-top: 8px;
    font-size: 16px;
    letter-spacing: .6px;
    color: var(--ink);
  }
  .divider {
    position: absolute;
    top: 108px; left: 290px;
    width: 2px; height: 90px;
    background: var(--accent);
  }
  .contact {
    position: absolute;
    top: 108px; left: 312px;
    list-style: none;
  }
  .contact__item {
    display: flex; align-items: center; gap: 10px;
    font-size: 16px; line-height: 23px;
    letter-spacing: .4px;
    color: var(--ink);
  }
  .contact__icon { width: 11px; height: 11px; flex: none; }
  .social {
    position: absolute;
    bottom: 30px; left: 0; right: 0;
    display: flex; align-items: center; justify-content: center; gap: 12px;
    font-size: 18px; letter-spacing: .4px;
  }
  .social__mark {
    width: 14px; height: 14px; border-radius: 50%;
    background: var(--accent);
  }
</style>
</head>
<body>

<section class="card card--front" aria-label="Card front">
  <div class="brand">
    <span class="brand__dot" aria-hidden="true"></span>
    <span class="brand__name">Tumble Trips</span>
  </div>
  <p class="tagline">Specializing in Glimmerland destinations, Pelican Bay Fun Park,<br>Cruises and All-Inclusive Vacations.</p>
</section>

<section class="card card--back" aria-label="Card back">
  <div class="person">
    <p class="person__name">Marla Quint</p>
    <p class="person__role">Owner</p>
  </div>
  <span class="divider" aria-hidden="true"></span>
  <ul class="contact">
    <li class="contact__item">
      <svg class="contact__icon" viewBox="0 0 12 12" aria-hidden="true"><rect x="3" y="0.5" width="6" height="11" rx="1.2" fill="none" stroke="#f47c20" stroke-width="1.3"/><circle cx="6" cy="9.3" r=".8" fill="#f47c20"/></svg>
      555-218-4603
    </li>
    <li class="contact__item">
      <svg class="contact__icon" viewBox="0 0 12 12" aria-hidden="true"><path d="M2.5 1 L4.5 1 L5 3.5 L3.8 4.5 Q5 7.2 7.5 8.2 L8.5 7 L11 7.5 L11 9.5 Q10.5 11 9 11 Q2 10 1 3 Q1 1.5 2.5 1Z" fill="#f47c20"/></svg>
      555-647-1925
    </li>
    <li class="contact__item">
      <svg class="contact__icon" viewBox="0 0 12 12" aria-hidden="true"><rect x="0.7" y="2.2" width="10.6" height="7.6" fill="none" stroke="#f47c20" stroke-width="1.2"/><path d="M1 2.5 L6 6.5 L11 2.5" fill="none" stroke="#f47c20" stroke-width="1.2"/></svg>
      Marla@TumbleTrips.example
    </li>
    <li class="contact__item">
      <svg class="contact__icon" viewBox="0 0 12 12" aria-hidden="true"><g fill="none" stroke="#f47c20" stroke-width="1"><circle cx="6" cy="6" r="5.2"/><ellipse cx="6" cy="6" rx="2.3" ry="5.2"/><path d="M0.8 6 H11.2 M1.6 3.3 H10.4 M1.6 8.7 H10.4"/></g></svg>
      www.TumbleTrips.example
    </li>
  </ul>
  <div class="social">
    <span>TumbleTrips</span>
    <span class="social__mark" aria-hidden="true"></span>
  </div>
</section>

</body>
</html>
```